Im open to ideas.. I was thinking on my business cards aswell as my logo. a place for my name. email. phone number and abn..

ive attched a file with my business logo. which i dont love the colours.. i was think a dark background with charcoal letters so something along those colour schumes but im open to ideas..

BRM Constructions

```html
<!DOCTYPE html>
<html lang="en">
<head>
<meta charset="utf-8">
<title>BRM Constructions – Business Cards</title>
<link href="https://fonts.googleapis.com/css2?family=Open+Sans:wght@400;600;700&display=swap" rel="stylesheet">
<style>
  :root {
    --bg-top: #2a2a2a;
    --bg-bottom: #050505;
    --card: #ffffff;
    --brand: #4a4a4a;
    --name: #6b6b6b;
    --muted: #9a9a9a;
    --icon: #8a8a8a;
  }
  * { margin: 0; padding: 0; box-sizing: border-box; }
  html, body { width: 1200px; height: 900px; overflow: hidden; }
  body {
    background: linear-gradient(180deg, var(--bg-top) 0%, #1a1a1a 45%, var(--bg-bottom) 100%);
    font-family: "Open Sans", Arial, sans-serif;
    position: relative;
  }
  .card {
    position: absolute;
    top: 306px;
    width: 440px;
    height: 271px;
    background: var(--card);
    border-radius: 12px;
  }
  .card--front { left: 149px; }
  .card--back { left: 608px; }

  .brand {
    position: absolute;
    text-align: center;
    color: var(--brand);
    font-weight: 700;
    line-height: 1;
  }
  .brand__main { display: block; }
  .brand__sub { display: block; }

  .card--front .brand { left: 36px; top: 118px; width: 192px; }
  .card--front .brand__main { font-size: 40px; letter-spacing: 3px; }
  .card--front .brand__sub { font-size: 8px; letter-spacing: 3.4px; margin-top: 4px; }

  .card--back .brand { left: 88px; top: 104px; width: 264px; }
  .card--back .brand__main { font-size: 56px; letter-spacing: 4px; }
  .card--back .brand__sub { font-size: 11px; letter-spacing: 4.8px; margin-top: 6px; }

  .contact {
    position: absolute;
    left: 247px;
    top: 72px;
  }
  .contact__name { font-size: 15px; font-weight: 600; color: var(--name); line-height: 18px; }
  .contact__role { font-size: 12px; color: var(--muted); line-height: 16px; }
  .contact__abn { font-size: 12px; color: var(--muted); margin-top: 16px; line-height: 16px; }
  .contact__abn b { color: var(--name); font-weight: 600; }
  .contact__list { list-style: none; margin-top: 13px; }
  .contact__item {
    display: flex; align-items: center;
    font-size: 12px; color: var(--muted); line-height: 16px;
  }
  .contact__item svg { width: 9px; height: 9px; margin-right: 7px; fill: var(--icon); flex: none; }
</style>
</head>
<body>
  <section class="card card--front">
    <div class="brand">
      <span class="brand__main">BRM</span>
      <span class="brand__sub">CONSTRUCTIONS</span>
    </div>
    <div class="contact">
      <p class="contact__name">Daniel Hart</p>
      <p class="contact__role">Managing Director</p>
      <p class="contact__abn"><b>ABN :</b> 12345678</p>
      <ul class="contact__list">
        <li class="contact__item">
          <svg viewBox="0 0 10 10" aria-hidden="true"><path d="M2 0.5 L3.6 2.6 L2.8 3.6 C3.4 5 4.9 6.5 6.4 7.2 L7.4 6.4 L9.5 8 L8.4 9.5 C4.5 9.2 0.8 5.5 0.5 1.6 Z"/></svg>
          044-987 654 321
        </li>
        <li class="contact__item">
          <svg viewBox="0 0 10 10" aria-hidden="true"><path d="M0.5 2 H9.5 V8 H0.5 Z M1 2.4 L5 5.4 L9 2.4" fill="var(--icon)" stroke="#fff" stroke-width="0.8"/></svg>
          info@brmbuild.com
        </li>
        <li class="contact__item">
          <svg viewBox="0 0 10 10" aria-hidden="true"><circle cx="5" cy="5" r="4.5"/><path d="M3 2.5 Q4.5 3.5 3.8 5 L5.5 6.5 L5 8.5 M6.5 2 L7.5 3.8 L6.3 4.5" stroke="#fff" stroke-width="0.8" fill="none"/></svg>
          www.brmbuild.com
        </li>
      </ul>
    </div>
  </section>

  <section class="card card--back">
    <div class="brand">
      <span class="brand__main">BRM</span>
      <span class="brand__sub">CONSTRUCTIONS</span>
    </div>
  </section>
</body>
</html>
```